New Company Business Card design

Looking for a corporate looking business card utilising my new logo design - the logo i would like embossed as one option and flat as another - simplistic but stylish - less is more - we are an import export business launching into the market - i would like a couple of options as main background - Grey or Black

```html
<!DOCTYPE html>
<html lang="en">
<head>
<meta charset="utf-8">
<title>Meridian Trade Partners – Business Card</title>
<link rel="stylesheet" href="https://fonts.googleapis.com/css2?family=Cinzel:wght@500&family=Open+Sans:wght@400;700&display=swap">
<style>
  :root {
    --panel-dark: #2f3237;
    --panel-deep: #25282c;
    --accent-grey: #9a9a9a;
    --text-grey: #7d7d7d;
    --card-white: #ffffff;
    --backdrop: #e9e7e4;
    --ink-white: #ffffff;
    --ink-dark: #2f3237;
  }
  * { box-sizing: border-box; margin: 0; padding: 0; }
  html, body {
    width: 1200px; height: 997px; overflow: hidden;
    background: var(--backdrop);
    font-family: "Open Sans", Arial, sans-serif;
  }
  .stage { position: relative; width: 1200px; height: 997px; }
  .card {
    position: absolute;
    width: 530px; height: 303px;
    box-shadow: 0 6px 18px rgba(0,0,0,0.12);
    overflow: hidden;
  }
  /* Front */
  .card-front { left: 55px; top: 347px; background: var(--card-white); }
  .front-wave { position: absolute; inset: 0; }
  .holder { position: absolute; right: 26px; top: 20px; text-align: right; }
  .holder-name {
    font-weight: 700; font-size: 13px; letter-spacing: 0.5px; color: var(--ink-dark);
  }
  .holder-role { font-size: 11px; color: #444; margin-top: 2px; }
  .brand { position: absolute; left: 30px; top: 84px; }
  .brand-row { display: flex; align-items: center; gap: 10px; }
  .brand-dot {
    width: 20px; height: 20px; border-radius: 50%; background: var(--panel-dark);
  }
  .brand-name {
    font-family: "Cinzel", Georgia, serif; font-weight: 500;
    font-size: 19px; color: var(--ink-dark); letter-spacing: 0.5px; white-space: nowrap;
  }
  .brand-rule { height: 1px; background: var(--accent-grey); margin: 6px 0 4px; width: 255px; }
  .brand-tagline {
    font-family: "Cinzel", Georgia, serif; font-size: 8.5px;
    letter-spacing: 2px; color: var(--text-grey); text-transform: uppercase;
  }
  .contacts {
    position: absolute; right: 22px; top: 118px; text-align: right;
    color: var(--ink-white); font-size: 11px; line-height: 17px;
  }
  .contact-line { display: flex; justify-content: flex-end; align-items: center; gap: 6px; }
  .contact-line svg { width: 11px; height: 11px; }
  .address {
    position: absolute; right: 22px; bottom: 40px;
    color: var(--ink-white); font-size: 11px;
  }
  /* Back */
  .card-back {
    left: 615px; top: 347px; background: var(--panel-dark);
    color: var(--ink-white); text-align: center;
  }
  .back-brand { position: absolute; left: 0; right: 0; top: 92px; }
  .back-brand .brand-row { justify-content: center; }
  .back-brand .brand-dot { background: var(--ink-white); }
  .back-brand .brand-name { color: var(--ink-white); font-size: 22px; }
  .back-brand .brand-rule { background: rgba(255,255,255,0.8); margin: 8px auto 5px; width: 290px; }
  .back-brand .brand-tagline { color: rgba(255,255,255,0.85); }
  .back-web {
    position: absolute; left: 0; right: 0; bottom: 40px;
    display: flex; justify-content: center; align-items: center; gap: 10px;
    font-size: 12px; letter-spacing: 0.8px;
  }
  .back-web .web-rule { width: 70px; height: 1px; background: rgba(255,255,255,0.8); }
</style>
</head>
<body>
<main class="stage">

  <section class="card card-front" aria-label="Business card front">
    <svg class="front-wave" viewBox="0 0 530 303" preserveAspectRatio="none" aria-hidden="true">
      <path d="M70,285 C220,275 290,215 340,160 C385,110 440,70 530,58" fill="none" stroke="#9a9a9a" stroke-width="8"/>
      <path d="M0,303 L0,294 C160,294 260,240 315,180 C365,125 430,82 530,76 L530,303 Z" fill="#2f3237"/>
      <path d="M120,290 C230,278 285,230 330,180" fill="none" stroke="#ffffff" stroke-width="1.5" opacity="0.6"/>
    </svg>

    <div class="holder">
      <p class="holder-name">ALAN BROOKS</p>
      <p class="holder-role">President</p>
    </div>

    <div class="brand">
      <div class="brand-row">
        <span class="brand-dot"></span>
        <span class="brand-name">Meridian Trade Partners</span>
      </div>
      <div class="brand-rule"></div>
      <p class="brand-tagline">Connecting Markets Worldwide</p>
    </div>

    <div class="contacts">
      <p class="contact-line">(000) 555-0199
        <svg viewBox="0 0 12 12" aria-hidden="true"><path d="M2.5 1l2 2.5-1 1.2c.7 1.4 1.6 2.3 3 3l1.2-1 2.5 2-1 1.8C5.5 10.5 1.5 6.5 1 2.2z" fill="#fff"/></svg>
      </p>
      <p class="contact-line">info@meridiantrade.com
        <svg viewBox="0 0 12 12" aria-hidden="true"><rect x="1" y="2.5" width="10" height="7" fill="none" stroke="#fff" stroke-width="1.2"/><path d="M1 2.5l5 4 5-4" fill="none" stroke="#fff" stroke-width="1.2"/></svg>
      </p>
      <p class="contact-line">www.meridiantrade.com
        <svg viewBox="0 0 12 12" aria-hidden="true"><circle cx="6" cy="6" r="4.8" fill="none" stroke="#fff" stroke-width="1.1"/><ellipse cx="6" cy="6" rx="2" ry="4.8" fill="none" stroke="#fff" stroke-width="1"/><path d="M1.2 6h9.6" stroke="#fff" stroke-width="1"/></svg>
      </p>
    </div>

    <p class="address">P.O. Box 48, Harbor Road, Portview, Zip Code - 10400</p>
  </section>

  <section class="card card-back" aria-label="Business card back">
    <div class="back-brand">
      <div class="brand-row">
        <span class="brand-dot"></span>
        <span class="brand-name">Meridian Trade Partners</span>
      </div>
      <div class="brand-rule"></div>
      <p class="brand-tagline">Connecting Markets Worldwide</p>
    </div>
    <p class="back-web"><span class="web-rule"></span>www.meridiantrade.com<span class="web-rule"></span></p>
  </section>

</main>
</body>
</html>
```